Create Website for new company called "Verdale Lodge 37"

Verdale Lodge 37 is a new business situated in Southwestern Colorado. We are creating a business that will rent out spaces where clients can grow their own marijuana. Picture a large green house with partitioned spaces that are secured by a lock. Best way to envision this would be to think of a storage business that rents out storage rooms. The difference is that we will be having the units inside a green house ( for growing purposes) Picture a small area that is secured by locks, Picture an area that has the ability to provide state of the art security, cameras etc. We want to focus our efforts on professionals, blue collar workers and end users of marijuana. Our emphasis is in the area of assisting those whom wish to grow their own plants. We want to provide them a safe facility in which to do that. . Keep in mind that we also build custom grow rooms at clients homes and provide a grow pod (lease these) where a small grow unit will be delivered and picked up from our clients whom want to lease a unit for a short amount of time. We have a business card ( just designed) and will send that information to those whom express an interests in this project. We want to be able to sign people up for our services by entering an agreement and signing the agreement while on the internet. We want to provide our services to those whom consume recreational and medical marijuana. This site will need to gather information I.e email addresses so that we can followup with offers. This is a tremendous opportunity for the right designer. We will be creating many more websites as other states come on line and make marijuana legal to consume. Use the business card model for a point of reference of how we envision the concept. That is a business card we just recently printed. The hands and the plant is our logo so far. Open to suggestions. There will be three levels of service. Bronze, Silver, Gold or Platinum. We will also have a retail biz down the road but not at the present time.

Target Market(s)

Ages 21-60

Industry/Entity Type

Medical

Logo Text

Verdale Lodge 37.

Number of Pages Required

5+ page

Requirements
Must have
• Clean appearance not to busy , easily navigable from link to link, page to page. Must have ability down the road to enter into a contractual agreement via the website. Must use our provided logo and example of that is on our business card that will be uploaded here shortly. We would like to have the colors that are on the business card however if you have suggestions or color schemes that you want us to consider that is okay.
Nice to have
• Nice to have a animation of seed to weed and how clients can save a tremendous amount of money growing their own cannabis. Nice to have testimonial page or feedback page. Have a membership component to website,
Should not have
• No flashing lights, etc. Not to busy in terms of animations.

```html
<!DOCTYPE html>
<html lang="en">
<head>
<meta charset="utf-8">
<title>Verdale Lodge 37</title>
<link href="https://fonts.googleapis.com/css2?family=Open+Sans:ital,wght@0,400;0,600;1,400&family=Arimo:wght@400;700&display=swap" rel="stylesheet">
<style>
:root{
  --green:#0f7f3c;
  --green-dark:#0a6a30;
  --green-light:#1b9a4c;
  --ink:#333333;
  --text:#555555;
  --rule:#e2e2e2;
  --footer:#333333;
  --bg:#ffffff;
  --accent:#c8822f;
}
*{margin:0;padding:0;box-sizing:border-box}
html,body{width:843px;height:1200px;overflow:hidden;background:var(--bg)}
body{position:relative;font-family:"Open Sans",Arial,sans-serif;color:var(--text)}
.abs{position:absolute}
.brand{left:0;width:843px;top:50px;text-align:center}
.brand-name{font-family:"Arimo",Arial,sans-serif;font-weight:700;font-size:30px;color:var(--ink);letter-spacing:.5px;display:inline-flex;align-items:center;gap:8px}
.brand-mark{width:14px;height:14px;border-radius:50%;background:var(--green);display:inline-block}
.brand-tag{font-size:7px;color:var(--ink);margin-top:2px;font-family:"Open Sans",serif}
.nav{left:70px;top:114px;width:704px;height:50px;background:linear-gradient(var(--green-light),var(--green-dark));display:flex;box-shadow:0 10px 12px -8px rgba(0,0,0,.25)}
.nav a{flex:1;color:#fff;text-decoration:none;font-size:10px;display:flex;align-items:center;justify-content:center;border-right:1px solid rgba(255,255,255,.25);position:relative}
.nav a:last-child{border-right:0}
.nav a.active::after{content:"";position:absolute;bottom:-5px;left:50%;margin-left:-5px;border:5px solid transparent;border-top-color:var(--green-dark);border-bottom:0}
.photo{background:linear-gradient(160deg,#a9b89a 0%,#5f8f3c 45%,#3e6e2a 100%)}
.hero{left:70px;top:180px;width:704px;height:264px;box-shadow:0 14px 14px -10px rgba(0,0,0,.35)}
.caption{position:absolute;left:0;right:0;bottom:0;background:rgba(40,40,40,.7);color:#fff;display:flex;align-items:center;justify-content:space-between;padding:0 14px;font-family:"Arimo",Arial,sans-serif;font-weight:700}
.hero .caption{height:46px;font-size:18px}
.arrow{width:18px;height:18px;flex:none}
.section-title{font-family:"Arimo",Arial,sans-serif;font-weight:700;color:var(--ink);font-size:15px}
.services-title{left:0;width:843px;top:479px;text-align:center}
.services-intro{left:100px;width:643px;top:506px;text-align:center;font-size:9px;line-height:16px}
.card{top:555px;width:214px;height:153px;box-shadow:0 10px 10px -8px rgba(0,0,0,.35)}
.card .caption{height:37px;font-size:12.5px;padding:0 10px}
.card .arrow{width:16px;height:16px}
.divider{left:70px;width:704px;height:1px;background:var(--rule)}
.about-title{left:70px;top:778px}
.about-photo{left:70px;top:814px;width:266px;height:137px;background:linear-gradient(160deg,#cfd8d2 0%,#7ea55e 40%,#3f6b2c 100%)}
.about-text{left:70px;top:966px;width:270px;font-size:9px;line-height:15.6px}
.btn{left:70px;top:1042px;width:80px;height:29px;background:var(--green);color:#fff;font-size:11px;display:flex;align-items:center;justify-content:center}
.blog-title{left:379px;top:778px}
.post{left:379px;width:395px}
.post-date{font-family:"Arimo",Arial,sans-serif;font-weight:700;font-size:14px;color:var(--ink);line-height:24px;width:44px;border-right:1px solid var(--rule);height:46px}
.post-head{display:flex;align-items:flex-start}
.post-sub{font-style:italic;font-size:9px;color:var(--ink);padding-left:11px;margin-top:7px}
.post-body{font-size:9px;line-height:16px;margin-top:6px}
.read-more{font-size:9px;color:var(--green);margin-top:8px}
.footer{left:0;top:1112px;width:843px;height:88px;background:var(--footer);color:#eee;text-align:center}
.copyright{font-size:9px;margin-top:20px}
.social{display:flex;justify-content:center;gap:5px;margin-top:18px}
.social span{width:19px;height:19px;border-radius:50%;background:#fff;display:block}
</style>
</head>
<body>

<header class="abs brand">
  <div class="brand-name"><span class="brand-mark"></span>VERDALE LODGE 37</div>
  <div class="brand-tag">"supporting the care &amp; cultivation of cannabis"</div>
</header>

<nav class="abs nav">
  <a class="active">Home</a><a>About Us</a><a>Our Services</a><a>Blog</a><a>FAQ</a><a>Gallery</a><a>Contact Us</a>
</nav>

<section class="abs hero photo" role="img" aria-label="Greenhouse interior with rows of cannabis plants under a timber roof">
  <div class="caption">
    <svg class="arrow" viewBox="0 0 20 20"><circle cx="10" cy="10" r="8.5" fill="none" stroke="#fff" stroke-width="1.5"/><path d="M11.5 6 7.5 10l4 4" fill="none" stroke="#fff" stroke-width="2"/></svg>
    <span>Essent vituperata in ius, vis facer fuisset accusam ea, sit ut quaesti</span>
    <svg class="arrow" viewBox="0 0 20 20"><circle cx="10" cy="10" r="8.5" fill="none" stroke="#fff" stroke-width="1.5"/><path d="M8.5 6l4 4-4 4" fill="none" stroke="#fff" stroke-width="2"/></svg>
  </div>
</section>

<h2 class="abs section-title services-title">OUR SERVICES</h2>
<p class="abs services-intro">Erat maluisset constituam te eam, cu mea accumsan adolescens conclusionemque, an eam assum tantas. Per ex meis delicata theophrastus, est rebum aliquip instructior ei. Eam odio novum id, cum appareat gubergren cotidieque.</p>

<article class="abs card photo" style="left:70px;background:linear-gradient(160deg,#b9d4d8,#6a9a8a 60%,#4f7a4e)" role="img" aria-label="Secured greenhouse unit with wooden frame and clear panels">
  <div class="caption"><span>Mei idque harum dolores te</span><svg class="arrow" viewBox="0 0 20 20"><circle cx="10" cy="10" r="8.5" fill="none" stroke="#fff" stroke-width="1.5"/><path d="M8.5 6l4 4-4 4" fill="none" stroke="#fff" stroke-width="2"/></svg></div>
</article>
<article class="abs card photo" style="left:313px;background:linear-gradient(160deg,#8a8a6a,#4e5a32 55%,#3a3a2a)" role="img" aria-label="Indoor grow room with potted cannabis plants">
  <div class="caption"><span>Et vim ridens oporteat glori</span><svg class="arrow" viewBox="0 0 20 20"><circle cx="10" cy="10" r="8.5" fill="none" stroke="#fff" stroke-width="1.5"/><path d="M8.5 6l4 4-4 4" fill="none" stroke="#fff" stroke-width="2"/></svg></div>
</article>
<article class="abs card photo" style="left:558px;background:linear-gradient(160deg,#7fa6d8,#9ab88a 50%,#4f7a34)" role="img" aria-label="Glass greenhouse pod in a garden">
  <div class="caption"><span>Lorem ipsum dolor sit</span><svg class="arrow" viewBox="0 0 20 20"><circle cx="10" cy="10" r="8.5" fill="none" stroke="#fff" stroke-width="1.5"/><path d="M8.5 6l4 4-4 4" fill="none" stroke="#fff" stroke-width="2"/></svg></div>
</article>

<div class="abs divider" style="top:748px"></div>

<h2 class="abs section-title about-title">ABOUT VERDALE LODGE</h2>
<div class="abs about-photo" role="img" aria-label="Polytunnel greenhouse with benches of young plants"></div>
<p class="abs about-text">Et odio nullam est, ad eum vulputate adipiscing, vis putant hendrerit theophrastus id. Labore perfecto forensibus ea vel, ne malis labores impedit vix.etiam detraxit phaedrum ne, nostrum molestiae eos ea.</p>
<div class="abs btn">Read More</div>

<h2 class="abs section-title blog-title">LATEST BLOG</h2>
<article class="abs post" style="top:806px">
  <div class="post-head"><div class="post-date">MAR<br>28</div><div class="post-sub">Mei idque harum dolores te, id putant sanctus fabulas</div></div>
  <p class="post-body">Et vim ridens oporteat gloriatur, no mei autem ipsum quaerendum. Ut mea reque harum mandamus. Augue necessitatibus ut duo.</p>
  <p class="read-more">Read More</p>
</article>
<div class="abs divider" style="top:936px;left:379px;width:395px"></div>
<article class="abs post" style="top:957px">
  <div class="post-head"><div class="post-date">MAR<br>30</div><div class="post-sub">Mei idque harum dolores te, id putant sanctus fabulas</div></div>
  <p class="post-body">Et vim ridens oporteat gloriatur, no mei autem ipsum quaerendum. Ut mea reque harum mandamus. Augue necessitatibus ut duo.</p>
  <p class="read-more">Read More</p>
</article>

<footer class="abs footer">
  <p class="copyright">Copyright @ 2014 Verdale Lodge 37.All Rights Reserved.</p>
  <div class="social"><span></span><span></span><span></span><span></span><span></span></div>
</footer>

</body>
</html>
```